FinTech company looking to revamp and expand client-facing interface for our financial models

Pellworth Engines currently has a very simple website that allows clients to interact with our financial models. We are looking to completely redesign the current site and add several extra pages to provide extra functionality. We want the design to have a modern, slick feel, that will work on both a desktop or a tablet. It should be straightforward for clients to move between different pages at any time, and clear from the layout how to interact with the more advanced features. We have included screenshots of existing pages in the attached design brief, as well as sketches of the functionality required by the new pages, but can't provide a direct link to the current site.
Target Market(s)
Professional investors that will be paying to access the interface
Industry/Entity Type
Finance
Number of Pages Required
4 page
Colors
Designer to choose colors to be used in the design.
Look and feel
Each slider illustrates characteristics of the customer's brand and the style your logo design should communicate.

```html
<!DOCTYPE html>
<html lang="en">
<head>
<meta charset="utf-8">
<title>Pellworth Engines – Models</title>
<link href="https://fonts.googleapis.com/css2?family=Lora:wght@400;700&family=Lato:wght@400;700&display=swap" rel="stylesheet">
<style>
:root{
  --page-bg:#ececec;
  --navy:#1f2a78;
  --navy-line:#34409a;
  --orange:#f08a2a;
  --orange-light:#f4a04a;
  --orange-dark:#e67a1a;
  --text:#333;
  --muted:#888;
  --row-alt:#ececec;
  --border:#d8d8d8;
  --white:#fff;
}
*{box-sizing:border-box;margin:0;padding:0}
html,body{width:1156px;height:1200px;overflow:hidden;background:var(--page-bg)}
body{font-family:"Lora",Georgia,serif;color:var(--text);position:relative}
.screen{position:absolute;left:55px;width:1045px;height:520px;background:var(--white);box-shadow:0 2px 10px rgba(0,0,0,.12);overflow:hidden}
.screen--models{top:62px}
.screen--factors{top:617px}

.brand{position:absolute;left:0;top:0;width:169px;height:54px;background:linear-gradient(180deg,var(--orange-light),var(--orange-dark));display:flex;align-items:center;justify-content:center;color:var(--white);font-weight:700;font-size:20px;letter-spacing:.3px}
.brand::after{content:"";position:absolute;right:-8px;top:19px;border-left:8px solid var(--orange);border-top:8px solid transparent;border-bottom:8px solid transparent}
.topbar{position:absolute;left:169px;right:0;top:0;height:54px;box-shadow:0 3px 6px rgba(0,0,0,.05);z-index:1}
.period-nav{position:absolute;left:18px;top:19px;font-size:10.5px;color:#555;word-spacing:3px}
.search{position:absolute;left:585px;top:14px;width:195px;height:26px;border:1px solid #e4e4e4;border-radius:13px;box-shadow:0 1px 3px rgba(0,0,0,.08)}
.search span{position:absolute;left:14px;top:7px;font-size:8px;color:var(--muted)}
.search .go{position:absolute;right:3px;top:3px;width:20px;height:20px;border-radius:50%;background:var(--orange)}
.bell{position:absolute;left:801px;top:17px}
.avatar{position:absolute;left:882px;top:12px;width:31px;height:31px;border-radius:50%;background:radial-gradient(circle at 50% 40%,#8aa3b8,#4a6a86)}

.sidebar{position:absolute;left:0;top:54px;bottom:0;width:169px;background:var(--navy)}
.menu-box{position:absolute;left:11px;width:148px;height:30px;border:1px solid var(--navy-line);color:var(--white);font-size:9px;display:flex;align-items:center;padding-left:11px;gap:7px}
.menu-box .chev{position:absolute;right:11px;top:9px}
.submenu{position:absolute;left:36px;top:50px;list-style:none;color:var(--white);font-size:9px;line-height:17.6px}

.main{position:absolute;left:169px;right:0;top:54px;bottom:0}
.filter{position:absolute;left:19px;display:flex;align-items:center;font-size:9.5px}
.filter .name{width:47px}
.filter .label{font-weight:700;width:76px;font-size:9px}
.filter .input{width:143px;height:24px;border:1px solid #bbb;border-radius:2px;font-size:8px;color:var(--muted);padding:7px 9px}
.export{position:absolute;left:19px;display:flex;align-items:center;gap:6px;color:var(--orange);font-weight:700;font-size:11px}

.data{position:absolute;left:19px;width:838px;border-collapse:collapse;table-layout:fixed;font-size:9.2px}
.data th{height:26px;background:linear-gradient(180deg,var(--orange-light),var(--orange-dark));color:var(--white);font-weight:700;text-align:left;padding:0 14px;font-size:9px;border-right:1px solid rgba(255,255,255,.35)}
.data td{height:40px;vertical-align:top;padding:8px 12px 0 14px;border:1px solid var(--border);line-height:12.5px}
.data--factors td{vertical-align:middle;padding-top:0}
.data tbody tr:nth-child(even) td{background:var(--row-alt)}
.sort{display:inline-block;margin-left:5px;border-top:4px solid var(--white);border-left:3px solid transparent;border-right:3px solid transparent;vertical-align:middle}

.footer{position:absolute;left:169px;right:0;bottom:0;height:54px;border-top:1px solid #eee;box-shadow:0 -3px 6px rgba(0,0,0,.04);font-family:"Lato",Arial,sans-serif;font-size:9px;color:#333;text-align:center;padding-top:22px}
</style>
</head>
<body>

<section class="screen screen--models">
  <div class="brand">PELLWORTH</div>
  <header class="topbar">
    <nav class="period-nav">250D | 83D | 42D</nav>
    <div class="search"><span>Search..</span><div class="go"><svg width="20" height="20" viewBox="0 0 20 20"><circle cx="9.5" cy="9.5" r="2.6" fill="none" stroke="#fff" stroke-width="1.3"/><line x1="11.4" y1="11.4" x2="13.2" y2="13.2" stroke="#fff" stroke-width="1.3"/></svg></div></div>
    <svg class="bell" width="18" height="20" viewBox="0 0 18 20"><path d="M8 2 C4 2 3 5 3 9 L3 13 L1 15 L15 15 L13 13 L13 9 C13 5 12 2 8 2Z" fill="none" stroke="#333" stroke-width="1.1"/><circle cx="13" cy="15" r="3.4" fill="#fff" stroke="#333" stroke-width="1"/><path d="M11.5 15 L12.6 16 L14.5 14" fill="none" stroke="#333" stroke-width="1"/></svg>
    <div class="avatar" role="img" aria-label="User profile photo"></div>
  </header>
  <aside class="sidebar">
    <div class="menu-box" style="top:12px"><svg width="9" height="8" viewBox="0 0 9 8"><path d="M4.5 0 L9 4 L7.8 4 L7.8 8 L5.5 8 L5.5 5.5 L3.5 5.5 L3.5 8 L1.2 8 L1.2 4 L0 4Z" fill="#fff"/></svg>MODELS<svg class="chev" width="7" height="7" viewBox="0 0 7 7"><path d="M1 3.5 L3.5 1 L6 3.5 M1 6 L3.5 3.5 L6 6" fill="none" stroke="#fff" stroke-width="1"/></svg></div>
    <ul class="submenu"><li>EQUITIES</li><li>ETFS</li><li>PAIRS</li><li>EIF PAIRS</li><li>FACTORS</li></ul>
    <div class="menu-box" style="top:146px"><svg width="9" height="9" viewBox="0 0 9 9"><circle cx="4.5" cy="4.5" r="3.2" fill="none" stroke="#fff" stroke-width="2.2" stroke-dasharray="1.6 0.9"/><circle cx="4.5" cy="4.5" r="1" fill="#fff"/></svg>SENSITIVITIES<svg class="chev" width="7" height="7" viewBox="0 0 7 7"><path d="M1 1 L3.5 3.5 L6 1 M1 3.5 L3.5 6 L6 3.5" fill="none" stroke="#fff" stroke-width="1"/></svg></div>
    <div class="menu-box" style="top:186px"><svg width="9" height="9" viewBox="0 0 10 10"><path d="M5 0 L6.2 3.6 L10 3.7 L7 6 L8.1 9.7 L5 7.5 L1.9 9.7 L3 6 L0 3.7 L3.8 3.6Z" fill="#fff"/></svg>FAVOURITES<svg class="chev" width="7" height="7" viewBox="0 0 7 7"><path d="M1 1 L3.5 3.5 L6 1 M1 3.5 L3.5 6 L6 3.5" fill="none" stroke="#fff" stroke-width="1"/></svg></div>
  </aside>
  <main class="main">
    <div class="filter" style="top:20px"><span class="name">Quality</span><span class="label">THRESHOLD :</span><span class="input">-10</span></div>
    <div class="filter" style="top:55px"><span class="name"><b>Abs.</b> <sup style="font-size:5px">Stat</sup></span><span class="label">THRESHOLD :</span><span class="input">-10</span></div>
    <div class="export" style="top:92px"><svg width="12" height="11" viewBox="0 0 12 11"><path d="M6 1 L1 1 L1 10 L10 10 L10 6" fill="none" stroke="#f08a2a" stroke-width="1.3"/><path d="M7 0.6 L11.4 0.6 L11.4 5 M11.4 0.6 L5.5 6.5" fill="none" stroke="#f08a2a" stroke-width="1.3"/></svg>EXPORT</div>
    <table class="data" style="top:128px">
      <colgroup><col style="width:67px"><col style="width:92px"><col style="width:83px"><col style="width:83px"><col style="width:63px"><col style="width:65px"><col style="width:64px"><col style="width:64px"><col style="width:64px"><col style="width:64px"><col style="width:64px"><col style="width:65px"></colgroup>
      <thead><tr><th style="padding-left:22px">ID<span class="sort"></span></th><th>SECTOR</th><th>TIME</th><th>QUALITY</th><th>STAT 1</th><th>STAT 2</th><th>STAT 3</th><th>STAT 4</th><th>STAT 5</th><th>STAT 6</th><th>STAT 7</th><th>STAT 8</th></tr></thead>
      <tbody>
        <tr><td>Model 1</td><td>Materials</td><td>2019-07-03 -<br>12:15:00.000</td><td>30.2288</td><td>2.01574</td><td>23.305</td><td>-0.149368</td><td>22.3054</td><td>4.63714</td><td>0.945706</td><td>2.81949</td><td>2.60858</td></tr>
        <tr><td>Model 2</td><td>Industrials</td><td>2019-07-03 -<br>12:15:00.000</td><td>45.6856</td><td>2.01574</td><td>23.305</td><td>-0.149368</td><td>22.3054</td><td>4.63714</td><td>0.945706</td><td>2.81949</td><td>2.60858</td></tr>
        <tr><td>Model 3</td><td>Consumer Discretionary</td><td>2019-07-03 -<br>12:15:00.000</td><td>30.2288</td><td>2.01574</td><td>23.305</td><td>-0.149368</td><td>22.3054</td><td>4.63714</td><td>0.945706</td><td>2.81949</td><td>2.60858</td></tr>
        <tr><td>Model 4</td><td>Information Technology</td><td>2019-07-03 -<br>12:15:00.000</td><td>45.6856</td><td>-0.569222</td><td>23.305</td><td>-0.149368</td><td>22.3054</td><td>4.63714</td><td>0.945706</td><td>2.81949</td><td>2.60858</td></tr>
        <tr><td>Model 5</td><td>Information Technology</td><td>2019-07-03 -<br>12:15:00.000</td><td>75.7733</td><td>2.01574</td><td>23.305</td><td>-0.149368</td><td>22.3054</td><td>4.63714</td><td>0.945706</td><td>2.81949</td><td>2.60858</td></tr>
      </tbody>
    </table>
  </main>
  <footer class="footer">Copyrights © 2019, Pellworth.All Rights Reserved &nbsp;|&nbsp; Privacy policy</footer>
</section>

<section class="screen screen--factors">
  <div class="brand">PELLWORTH</div>
  <header class="topbar">
    <nav class="period-nav">250D | 83D | 42D</nav>
    <div class="search"><span>Search..</span><div class="go"><svg width="20" height="20" viewBox="0 0 20 20"><circle cx="9.5" cy="9.5" r="2.6" fill="none" stroke="#fff" stroke-width="1.3"/><line x1="11.4" y1="11.4" x2="13.2" y2="13.2" stroke="#fff" stroke-width="1.3"/></svg></div></div>
    <svg class="bell" width="18" height="20" viewBox="0 0 18 20"><path d="M8 2 C4 2 3 5 3 9 L3 13 L1 15 L15 15 L13 13 L13 9 C13 5 12 2 8 2Z" fill="none" stroke="#333" stroke-width="1.1"/><circle cx="13" cy="15" r="3.4" fill="#fff" stroke="#333" stroke-width="1"/><path d="M11.5 15 L12.6 16 L14.5 14" fill="none" stroke="#333" stroke-width="1"/></svg>
    <div class="avatar" role="img" aria-label="User profile photo"></div>
  </header>
  <aside class="sidebar">
    <div class="menu-box" style="top:12px"><svg width="9" height="8" viewBox="0 0 9 8"><path d="M4.5 0 L9 4 L7.8 4 L7.8 8 L5.5 8 L5.5 5.5 L3.5 5.5 L3.5 8 L1.2 8 L1.2 4 L0 4Z" fill="#fff"/></svg>MODELS<svg class="chev" width="7" height="7" viewBox="0 0 7 7"><path d="M1 3.5 L3.5 1 L6 3.5 M1 6 L3.5 3.5 L6 6" fill="none" stroke="#fff" stroke-width="1"/></svg></div>
    <ul class="submenu"><li>EQUITIES</li><li>ETFS</li><li>PAIRS</li><li>EIF PAIRS</li><li>FACTORS</li></ul>
    <div class="menu-box" style="top:146px"><svg width="9" height="9" viewBox="0 0 9 9"><circle cx="4.5" cy="4.5" r="3.2" fill="none" stroke="#fff" stroke-width="2.2" stroke-dasharray="1.6 0.9"/><circle cx="4.5" cy="4.5" r="1" fill="#fff"/></svg>SENSITIVITIES<svg class="chev" width="7" height="7" viewBox="0 0 7 7"><path d="M1 1 L3.5 3.5 L6 1 M1 3.5 L3.5 6 L6 3.5" fill="none" stroke="#fff" stroke-width="1"/></svg></div>
    <div class="menu-box" style="top:186px"><svg width="9" height="9" viewBox="0 0 10 10"><path d="M5 0 L6.2 3.6 L10 3.7 L7 6 L8.1 9.7 L5 7.5 L1.9 9.7 L3 6 L0 3.7 L3.8 3.6Z" fill="#fff"/></svg>FAVOURITES<svg class="chev" width="7" height="7" viewBox="0 0 7 7"><path d="M1 1 L3.5 3.5 L6 1 M1 3.5 L3.5 6 L6 3.5" fill="none" stroke="#fff" stroke-width="1"/></svg></div>
  </aside>
  <main class="main">
    <div class="filter" style="top:13px"><span class="name"><b>Stat 1</b></span><span class="label">THRESHOLD :</span><span class="input">-10</span></div>
    <div class="filter" style="top:46px"><span class="name"><b>Stat 2</b></span><span class="label">THRESHOLD :</span><span class="input">-10</span></div>
    <div class="filter" style="top:79px"><span class="name"><b>Stat 3</b></span><span class="label">THRESHOLD :</span><span class="input">-10</span></div>
    <div class="export" style="top:114px"><svg width="12" height="11" viewBox="0 0 12 11"><path d="M6 1 L1 1 L1 10 L10 10 L10 6" fill="none" stroke="#f08a2a" stroke-width="1.3"/><path d="M7 0.6 L11.4 0.6 L11.4 5 M11.4 0.6 L5.5 6.5" fill="none" stroke="#f08a2a" stroke-width="1.3"/></svg>EXPORT</div>
    <table class="data data--factors" style="top:144px">
      <colgroup><col style="width:111px"><col style="width:90px"><col style="width:123px"><col style="width:86px"><col style="width:87px"><col style="width:86px"><col style="width:85px"><col style="width:85px"><col style="width:85px"></colgroup>
      <thead><tr><th>FACTOR</th><th>ID<span class="sort"></span></th><th>SECTOR</th><th>STAT 1</th><th>STAT 2</th><th>STAT 3</th><th>STAT 4</th><th>STAT 5</th><th>STAT 6</th></tr></thead>
      <tbody>
        <tr><td>Factor 1</td><td>Model 1</td><td>Materials</td><td>2.01574</td><td>23.305</td><td>-0.149368</td><td>22.3054</td><td>4.63714</td><td>0.945706</td></tr>
        <tr><td>Factor 2</td><td>Model 1</td><td>Materials</td><td>2.01574</td><td>23.305</td><td>-0.149368</td><td>22.3054</td><td>4.63714</td><td>0.945706</td></tr>
        <tr><td>Factor 3</td><td>Model 1</td><td>Materials</td><td>2.01574</td><td>23.305</td><td>-0.149368</td><td>22.3054</td><td>4.63714</td><td>0.945706</td></tr>
        <tr><td>Factor 4</td><td>Model 2</td><td>Industrials</td><td>-0.569222</td><td>23.305</td><td>-0.149368</td><td>22.3054</td><td>4.63714</td><td>0.945706</td></tr>
        <tr><td>Factor 5</td><td>Model 2</td><td>Industrials</td><td>2.01574</td><td>23.305</td><td>-0.149368</td><td>22.3054</td><td>4.63714</td><td>0.945706</td></tr>
      </tbody>
    </table>
  </main>
  <footer class="footer">Copyrights © 2019, Pellworth.All Rights Reserved &nbsp;|&nbsp; Privacy policy</footer>
</section>

</body>
</html>
```